Tri-Fold Brochure for Christian Author and Speaker

Lorna Whitfield is an inspirational author and speaker, sharing her testimony and encouraging others in their walk with Christ. A gifted writer, her work has been featured on Gently Radiant, Steadfast Mornings, and Hymns & Teacups Magazine (Fall 2011).

Lorna ‘s first book, Leaving the Lantern Room: Unmasking Hidden Snares in Ordinary Living, is an informative memoir and Bible study, recounting her journey from committed Christian to witch, medium, and ghost hunter for eight years until restored to faith in Jesus Christ. She was a contributing author to Walking Past the Shadows: A Candid View of Sorcery from Those Who Left by Dale Pennington and a consultant for the novel The Keeper of Marlow Hollow by Beacon Prize Winning Author, Helen Osgood.

Lorna’s second book, An Insider’s Guide to Spiritual Warfare: 20 Battle-Tested Strategies from Behind Enemy Lines, will be published by Harvest Lane Press for Fall 2014.

Lorna is a wife and mother. She enjoys writing, spending time with her family, taking long walks, listening to music of all kinds, and experiencing God’s daily gift called life.

You can read more about Lorna and see the look and feel we are going for at www.lornawhitfield.example

The brochure is to be used as a promotional tool to gain Lorna speaking engagements. You can see the topics she covers at http://www.lornawhitfield.example/speaking-engagements/.

More info can be found at: https://www.facebook.com/AuthorLornaWhitfield
https://www.facebook.com/VMUCX
https://www.facebook.com/LeavingtheLanternRoom
https://www.facebook.com/OpenDoorOutreach
http://www.opendooroutreach.example

I have uploaded 3 headshots, book covers for both of Lorna's books and the design layout in .EPS format from Swiftprintery.example where I will be getting printing done.

3 more days till the contest ends get your final designs in.

Reason: I'm extending this as I am tied up at a leadership conference and will not be able to give this the attention it deserves till the weekend.

Target Market(s)

Churches and women's groups. Lorna's current audience skews heavy to women on a 70/30 ratio.

Industry/Entity Type

Christian

Requirements
Must have
• Headshot I have uploaded 3
Quotes from previous speaking engagements you can find those at http://www.lornawhitfield.example/speaking-engagements/

```html
<!DOCTYPE html>
<html lang="en">
<head>
<meta charset="utf-8">
<title>Speaking – Lorna Whitfield</title>
<link rel="stylesheet" href="https://fonts.googleapis.com/css2?family=Jost:wght@300;400;600;700&display=swap">
<style>
  :root {
    --magenta: #b4124f;
    --magenta-soft: #c93a6c;
    --blush: #fbe9ee;
    --blush-deep: #f4cfd9;
    --ink: #4a3940;
    --ink-dark: #3a2a30;
    --white: #ffffff;
  }
  * { margin: 0; padding: 0; box-sizing: border-box; }
  html, body { width: 848px; height: 1200px; overflow: hidden; }
  body { font-family: "Jost", "Futura", sans-serif; color: var(--ink); }
  .page {
    position: relative; width: 848px; height: 1200px; overflow: hidden;
    background: var(--blush);
  }
  .floral-backdrop {
    position: absolute; inset: 0;
    background:
      radial-gradient(ellipse 420px 380px at 30% 48%, rgba(255,255,255,.75), transparent 70%),
      radial-gradient(ellipse 360px 320px at 80% 30%, rgba(255,255,255,.6), transparent 70%),
      radial-gradient(ellipse 500px 420px at 15% 12%, rgba(244,207,217,.7), transparent 70%),
      linear-gradient(160deg, #fbe3ea 0%, #fdf1f4 45%, #f8dde5 100%);
  }
  .top-strip { position: absolute; left: 0; top: 0; width: 848px; height: 11px; background: var(--magenta); }
  .title-tab {
    position: absolute; left: 57px; top: 0; width: 321px; height: 142px;
    background: var(--magenta); border-radius: 0 0 43px 43px;
    display: flex; align-items: center; justify-content: center;
  }
  .title-tab h1 { color: var(--white); font-weight: 300; font-size: 68px; letter-spacing: .5px; margin-top: 6px; }
  .intro {
    position: absolute; left: 67px; top: 77px; width: 724px;
    font-size: 18.5px; line-height: 31px; text-align: justify;
  }
  .intro .tab-space { float: left; width: 318px; height: 93px; }
  .hl { color: var(--magenta); }
  .topics { position: absolute; left: 110px; top: 266px; }
  .topics h2 { font-size: 18px; font-weight: 700; color: var(--magenta); margin-left: 18px; line-height: 31px; }
  .topics ul { list-style: none; }
  .topics li { font-size: 18px; line-height: 31.4px; color: var(--magenta); position: relative; padding-left: 18px; }
  .topics li::before { content: ""; position: absolute; left: 0; top: 12px; width: 9px; height: 9px; background: var(--magenta-soft); }
  .headshot {
    position: absolute; left: 546px; top: 218px; width: 201px; height: 276px;
    border: 4px solid var(--magenta);
    background: linear-gradient(170deg, #6f7b4e 0%, #8a6a52 45%, #c9b9b0 75%, #5b4a42 100%);
  }
  .testimonials-heading {
    position: absolute; left: 67px; top: 478px;
    font-size: 34px; font-weight: 700; color: var(--magenta); line-height: 48px;
  }
  .testimonial { position: absolute; top: 537px; }
  .testimonial.left { left: 67px; width: 336px; }
  .testimonial.right { left: 457px; width: 334px; }
  .testimonial h3 { font-size: 19.5px; font-weight: 400; line-height: 31px; color: var(--ink-dark); height: 93px; }
  .testimonial p { margin-top: 16px; font-size: 16.5px; line-height: 31px; text-align: justify; }
  .bottom-tab {
    position: absolute; left: 57px; top: 1112px; width: 734px; height: 88px;
    background: var(--magenta); border-radius: 43px 43px 0 0;
  }
  .bottom-strip { position: absolute; left: 0; top: 1180px; width: 848px; height: 20px; background: var(--magenta); }
</style>
</head>
<body>
<div class="page">
  <div class="floral-backdrop" role="img" aria-label="Soft pink lily flowers fading into the background"></div>
  <div class="top-strip"></div>
  <div class="title-tab"><h1>Speaking</h1></div>

  <p class="intro"><span class="tab-space"></span>As a speaker, <span class="hl">Lorna Whitfield</span> shares from her own life lessons and as a Biblical Counselor, encouraging others toward a deeper walk with God. Lorna offers sound, heartfelt, and practical biblical advice on issues relevant to the <span class="hl">21st Century Christian</span>. read more.....</p>

  <section class="topics">
    <h2>Speaking Topics Include:</h2>
    <ul>
      <li>Christians and the Occult</li>
      <li>Homelessness (with Grant Whitfield)</li>
      <li>Human Trafficking</li>
      <li>Marriage Restoration (with Grant Whitfield)</li>
      <li>Prayer as a Lifestyle</li>
      <li>Spiritual Warfare</li>
    </ul>
  </section>

  <div class="headshot" role="img" aria-label="Headshot of Lorna Whitfield"></div>

  <h2 class="testimonials-heading">What’s Lorna Like as A Speaker?</h2>

  <article class="testimonial left">
    <h3>Marian Ashcombe, Harborview<br>Community Church<br>Women’s Ministry:</h3>
    <p>The Women’s Ministry at Harborview Church in Alder Falls, MI invited <span class="hl">Lorna Whitfield</span> to speak at our Mother or Daughter Banquet earlier this month. I am so glad she accepted! We couldn’t have chosen a speaker to fit in better than <span class="hl">Lorna</span>. She took our theme, “Instruments”, and incorporated that into her speaking time with us. She used life examples and spoke directly into the hearts of the women and girls that attended our banquet. Read more.....</p>
  </article>

  <article class="testimonial right">
    <h3>Daniel Hargrove,<br>Kindred Crossroads Seminar Tent,<br>Coordinator:</h3>
    <p>“I was honored and delighted to have <span class="hl">Lorna Whitfield</span> be one of our speakers in the “Kindred Crossroads Seminar Tent” at Kindred Christian Music Festival in Bayport, Michigan (one of the nation’s top 10 Christian music festivals). Lorna has a unique testimony and style of speaking that keeps people, young and old, engaged into the heart of her message. Her stories of involvement in the occult and her conclusion of how God rescued her from these traps, answers many of the questions that people often have, read more.....</p>
  </article>

  <div class="bottom-tab"></div>
  <div class="bottom-strip"></div>
</div>
</body>
</html>
```